Business card for Eyelash extension salon in Westmere Hills,California USA

We need new business card for our salon in Westmere Hills. The salon name is 'Lashvera' . We would like to have...Business name: Lashvera Name of person: will provide later Address 4720 N.Alder Crest Ave Westmere Hills , CA 91999 Phone: will provide later (Text only) Web: www.lashverastudio.example Snapgrid icon, Circlebook icon follow us for seasonal campaign and news @lashverastudiolounge Design should look elegant, high-end, clean, simple, cohesive with my brand. Please refer my brand board. Business name color will be metallic bronzy color. Im thinking grey background or white background. Thanks

Target Market(s)

25-35. Gender neutral. People who are in Entertainment business industry.
This is High-end Eyelash extension salon in Westmere Hills

Industry/Entity Type

Beauty Salon

Contact Information for Business Card

Business name: Lashvera
Name of person: will provide later
Address 4720 N.Alder Crest Ave Westmere Hills , CA 91999
Phone: will provide later (Text only)
Web: www.lashverastudio.example
Snapgrid icon, Circlebook icon
follow us for seasonal campaign and news @lashverastudiolounge

Requirements
Must have
• Beautiful, elegant, clean and simple look but very attractive and modern
Should not have
• We don't like too clutter, too busy designs.

```html
<!DOCTYPE html>
<html lang="en">
<head>
<meta charset="utf-8">
<title>Lashvera Business Card</title>
<link rel="stylesheet" href="https://fonts.googleapis.com/css2?family=Playfair+Display:wght@800&family=Poppins:ital,wght@0,300;0,400;0,500;1,600&display=swap">
<style>
  :root {
    --backdrop: #2b2e33;
    --card-black: #0f0f10;
    --bronze: #b27c56;
    --bronze-soft: #a06f4d;
    --marble-light: #f6f6f7;
    --marble-vein: #d9dadd;
    --ink: #141414;
    --white: #ffffff;
  }
  * { box-sizing: border-box; margin: 0; padding: 0; }
  html, body {
    width: 1200px; height: 900px; overflow: hidden;
    background: var(--backdrop);
    font-family: "Poppins", sans-serif;
  }
  .stage {
    position: relative; width: 1200px; height: 900px;
    display: flex; align-items: center; justify-content: center; gap: 60px;
  }
  .card {
    position: relative; width: 500px; height: 286px;
    border-radius: 22px; overflow: hidden;
    box-shadow: 0 14px 30px rgba(0,0,0,.35);
  }
  .marble {
    background:
      radial-gradient(ellipse at 30% 40%, rgba(217,218,221,.7), transparent 55%),
      radial-gradient(ellipse at 75% 70%, rgba(217,218,221,.5), transparent 50%),
      linear-gradient(135deg, var(--marble-light), #ececee 50%, var(--marble-light));
  }

  /* Front */
  .card-front { background: var(--card-black); }
  .card-front .edge-strip {
    position: absolute; left: 0; top: 0; bottom: 0; width: 20px;
  }
  .brand {
    position: absolute; inset: 0 0 0 20px;
    display: flex; flex-direction: column; align-items: center; justify-content: center;
    color: var(--bronze);
  }
  .brand-name {
    font-weight: 300; font-size: 64px; letter-spacing: 2px; line-height: 1;
  }
  .brand-place {
    margin-top: 16px; font-weight: 400; font-size: 11px;
    letter-spacing: 5px; text-transform: uppercase; color: var(--bronze-soft);
  }

  /* Back */
  .card-back { background: var(--card-black); }
  .card-back .marble-field {
    position: absolute; left: 0; top: 0; right: 0; height: 192px;
  }
  .holder-name {
    position: absolute; right: 30px; top: 26px;
    font-family: "Playfair Display", serif; font-weight: 800;
    font-size: 30px; letter-spacing: 1px; color: var(--ink); text-transform: uppercase;
  }
  .contact-row {
    position: absolute; left: 30px; right: 30px; top: 108px;
    display: flex; align-items: stretch; gap: 18px;
    font-size: 12.5px; color: var(--ink); line-height: 1.55;
  }
  .contact-col { flex: 1; }
  .contact-col.left { text-align: right; }
  .contact-divider { width: 1px; background: var(--ink); }
  .social-band {
    position: absolute; left: 0; right: 0; top: 192px; bottom: 0;
    display: flex; flex-direction: column; align-items: center; justify-content: center; gap: 10px;
    color: var(--white);
  }
  .follow-line { font-style: italic; font-weight: 600; font-size: 13px; }
  .social-row { display: flex; align-items: center; gap: 18px; font-size: 12.5px; font-weight: 500; }
  .network { display: flex; align-items: center; gap: 6px; font-weight: 400; }
  .network-dot { width: 12px; height: 12px; border-radius: 50%; background: var(--white); }
</style>
</head>
<body>
<main class="stage">
  <section class="card card-front">
    <div class="edge-strip marble" role="img" aria-label="White marble texture strip"></div>
    <div class="brand">
      <span class="brand-name">Lashvera</span>
      <span class="brand-place">Westmere Hills</span>
    </div>
  </section>

  <section class="card card-back">
    <div class="marble-field marble" role="img" aria-label="White marble texture background"></div>
    <h1 class="holder-name">Marlowe Sinclair</h1>
    <div class="contact-row">
      <div class="contact-col left">
        <p>555 014 2368 <em>(Text only)</em></p>
        <p>www.lashverastudio.example</p>
      </div>
      <div class="contact-divider"></div>
      <div class="contact-col right">
        <p>4720 N.Alder Crest Ave</p>
        <p>Westmere Hills , CA 91999</p>
      </div>
    </div>
    <div class="social-band">
      <p class="follow-line">Follow us for seasonal campaign and news</p>
      <div class="social-row">
        <span class="network"><span class="network-dot"></span>Circlebook</span>
        <span class="handle">@lashverastudiolounge</span>
        <span class="network"><span class="network-dot"></span>Snapgrid</span>
      </div>
    </div>
  </section>
</main>
</body>
</html>
```